KDWB Business Card

Looking for a business card design to incorporate our branding. We want to only use the colors listing in the Branding Package (attached).
Updates

Target Market(s)

People who need their phone or device fixed.

Industry/Entity Type

Electronics

Contact Information for Business Card

Please use:

Brightwick Gadget Clinic LLC
4810 E Harlow Ridge Rd
Suite 417
San Antonio, TX 78163

Marcus Delgrove, Store Manager

(210) 555-0147

Requirements
Must have
• Must include the colors that are contained within the Branding Package PDF file.

```html
<!DOCTYPE html>
<html lang="en">
<head>
<meta charset="utf-8">
<title>Brightwick Gadget Clinic – Business Card</title>
<link href="https://fonts.googleapis.com/css2?family=Questrial&display=swap" rel="stylesheet">
<style>
  :root {
    --brand-orange: #f0562a;
    --ink-grey: #55575a;
    --stripe-grey: #5a5b5e;
    --paper: #ffffff;
    --backdrop: #2b2b2d;
  }
  * { margin: 0; padding: 0; box-sizing: border-box; }
  html, body { width: 1200px; height: 880px; overflow: hidden; }
  body {
    background: var(--backdrop);
    font-family: "Questrial", "Century Gothic", sans-serif;
    position: relative;
  }
  .card {
    position: absolute;
    width: 700px;
    height: 400px;
    border-radius: 26px;
    overflow: hidden;
  }
  .card-front {
    left: 80px; top: 30px;
    background: var(--brand-orange);
    display: flex; align-items: center; justify-content: center;
  }
  .card-back {
    left: 420px; top: 450px;
    background: var(--paper);
  }
  .brand-mark {
    display: flex; align-items: center; gap: 16px;
  }
  .brand-square {
    width: 46px; height: 46px;
    border-radius: 8px;
  }
  .brand-name {
    font-size: 40px; letter-spacing: 0.5px; white-space: nowrap;
  }
  .card-front .brand-square { background: var(--paper); }
  .card-front .brand-name { color: var(--paper); }
  .card-back .brand-mark {
    position: absolute; left: 44px; top: 70px;
  }
  .card-back .brand-square { background: var(--brand-orange); width: 40px; height: 40px; }
  .card-back .brand-name { color: var(--brand-orange); font-size: 32px; }
  .company-block {
    position: absolute; left: 44px; top: 226px;
    color: var(--ink-grey); font-size: 16px; line-height: 1.35;
  }
  .company-name { color: var(--brand-orange); font-size: 19px; margin-bottom: 4px; }
  .contact-block {
    position: absolute; right: 44px; top: 150px;
    text-align: left; color: var(--ink-grey); font-size: 15px; line-height: 1.3;
  }
  .person-name { color: var(--brand-orange); font-size: 21px; }
  .phone-line { display: flex; align-items: center; gap: 8px; margin-top: 8px; }
  .phone-icon {
    width: 20px; height: 20px; border-radius: 4px;
    background: var(--brand-orange);
    display: flex; align-items: center; justify-content: center;
  }
  .base-band { position: absolute; left: 0; top: 0; width: 700px; height: 400px; }
</style>
</head>
<body>

  <section class="card card-front" aria-label="Business card front">
    <div class="brand-mark">
      <span class="brand-square"></span>
      <span class="brand-name">Brightwick Gadget Clinic</span>
    </div>
  </section>

  <section class="card card-back" aria-label="Business card back">
    <svg class="base-band" viewBox="0 0 700 400" aria-hidden="true">
      <path fill="var(--stripe-grey)" d="M0 336 L526 336 L523 346 L0 346 Z"/>
      <path fill="var(--brand-orange)" d="M0 352 L518 352 Q532 352 535 338 L539 318 Q542 302 558 302 L700 302 L700 400 L0 400 Z"/>
    </svg>

    <div class="brand-mark">
      <span class="brand-square"></span>
      <span class="brand-name">Brightwick Gadget Clinic</span>
    </div>

    <div class="company-block">
      <p class="company-name">Brightwick Gadget Clinic LLC</p>
      <p class="address-line">4810 E Harlow Ridge Rd</p>
      <p class="address-line">Suite 417, San Antonio, TX 78163</p>
    </div>

    <div class="contact-block">
      <p class="person-name">Marcus Delgrove</p>
      <p class="person-title">Store Manager</p>
      <p class="phone-line">
        <span class="phone-icon">
          <svg width="13" height="13" viewBox="0 0 24 24" aria-hidden="true">
            <path fill="#fff" d="M6.6 10.8a15.1 15.1 0 0 0 6.6 6.6l2.2-2.2c.3-.3.7-.4 1-.2 1.1.4 2.3.6 3.6.6.6 0 1 .4 1 1V20c0 .6-.4 1-1 1C10.6 21 3 13.4 3 4c0-.6.4-1 1-1h3.5c.6 0 1 .4 1 1 0 1.3.2 2.5.6 3.6.1.3 0 .7-.2 1z"/>
          </svg>
        </span>
        <span class="phone-number">(210) 555-0147</span>
      </p>
    </div>
  </section>

</body>
</html>
```